Quorva - corporate Business Card

We need a good look and innovative business card for a new start up company based in Los Angeles called "Quorva". We are in a payment business, including payment card, app, and ewallet. We are expert in online payment and Card not present (CNP) transaction.
We need an innovative, modern business card.

Our logo font is Aero Matics

Target Market(s)

Startup - Bank - Online Payment - Card Manufacturing

Industry/Entity Type

Startup

Contact Information for Business Card

phone: 555 014 7396 - Address: 4172 Marlowe blvd, Larkmoor Heights, NV 89123

Requirements
Must have
• Message: innovative, professional, expert, high tech, trust, online payment expert, security
Nice to have
• no comment
Should not have
• no Comment

```html
<!DOCTYPE html>
<html lang="en">
<head>
<meta charset="UTF-8">
<title>Quorva – Business Card</title>
<link rel="stylesheet" href="https://fonts.googleapis.com/css2?family=Lato:wght@400;700&display=swap">
<style>
  :root {
    --backdrop: #c8c8c8;
    --brand-red: #b61d2d;
    --charcoal: #2e2e2e;
    --paper: #ffffff;
  }
  html, body {
    margin: 0;
    padding: 0;
    width: 1200px;
    height: 900px;
    overflow: hidden;
    background: var(--backdrop);
    font-family: "Lato", Arial, sans-serif;
  }
  .business-card {
    position: absolute;
    left: 180px;
    top: 190px;
    width: 840px;
    height: 519px;
    overflow: hidden;
    background: var(--charcoal);
  }
  .card-shapes {
    position: absolute;
    inset: 0;
  }
  .holder {
    position: absolute;
    right: 50px;
    top: 53px;
    text-align: right;
    color: var(--paper);
  }
  .holder-name {
    margin: 0;
    font-size: 23px;
    font-weight: 700;
    letter-spacing: 0.2px;
    line-height: 28px;
  }
  .holder-role {
    margin: 0;
    font-size: 21px;
    font-weight: 400;
    line-height: 30px;
  }
  .brand-name {
    position: absolute;
    left: 310px;
    top: 178px;
    margin: 0;
    font-size: 132px;
    font-weight: 700;
    line-height: 160px;
    color: var(--brand-red);
    letter-spacing: 1px;
  }
  .contact {
    position: absolute;
    right: 50px;
    top: 388px;
    text-align: right;
    color: var(--paper);
    font-size: 21px;
    font-style: normal;
    line-height: 31px;
  }
  .contact-phone {
    display: flex;
    justify-content: flex-end;
    align-items: center;
    gap: 10px;
    margin-bottom: 16px;
  }
  .phone-icon {
    width: 17px;
    height: 20px;
  }
</style>
</head>
<body>
  <main class="business-card">
    <svg class="card-shapes" width="840" height="519" viewBox="0 0 840 519" aria-hidden="true">
      <rect x="244" y="0" width="596" height="519" fill="var(--brand-red)"/>
      <circle cx="244" cy="260" r="260" fill="var(--brand-red)"/>
      <circle cx="244" cy="260" r="249" fill="var(--paper)"/>
      <rect x="244" y="146" width="596" height="223" fill="var(--paper)"/>
      <circle class="brand-mark" cx="187" cy="259" r="98" fill="var(--brand-red)"/>
    </svg>

    <header class="holder">
      <p class="holder-name">DARREN HOLLOWAY</p>
      <p class="holder-role">Managing Director</p>
    </header>

    <h1 class="brand-name">Quorva</h1>

    <address class="contact">
      <div class="contact-phone">
        <span>555 014 7396</span>
        <svg class="phone-icon" viewBox="0 0 24 28" aria-hidden="true">
          <path fill="var(--paper)" d="M6 1c1-.6 2-.4 2.6.6l3 5c.5.9.3 2-.5 2.6L9 10.8c1 3.2 2.8 6 5.3 8.1l2-1.4c.8-.6 1.9-.5 2.6.3l3.6 4.5c.7.9.6 2.1-.3 2.8l-2 1.6c-1.7 1.3-4 1.4-5.8.2C6.8 22.6 2.3 14.9 1.6 7.5 1.4 5.4 2.4 3.3 4.2 2.2z"/>
        </svg>
      </div>
      <div>4172 Marlowe blvd,</div>
      <div>Larkmoor Heights, NV 89123</div>
    </address>
  </main>
</body>
</html>
```